Business Card Design for Flood Rescue 360 - Property Restoration Professionals

I need a business card designed for Flood Rescue 360. We are a full-service property restoration solution. Providing water, fire, smoke & storm restoration as well as mold remediation and full remodel or reconstruction to homes and businesses across Dallas-Fort Worth, TX.
Target Market(s)
home and business owners with insurance covered property damage from water, fire or storm related damage
Industry/Entity Type
property restoration
Contact Information for Business Card
Marcus Pelley General Manager Cell: 214-555-0193 Office: 469-555-0148 email: Marcus@FloodRescue360.example services: Water, Fire, Mold, Reconstruction Tagline: Urgency for Your Water Emergency!
Look and feel
Each slider illustrates characteristics of the customer's brand and the style your logo design should communicate.

```html
<!DOCTYPE html>
<html lang="en">
<head>
<meta charset="UTF-8">
<title>Flood Rescue 360 – Business Card</title>
<link href="https://fonts.googleapis.com/css2?family=Montserrat:wght@400;500;700;800&display=swap" rel="stylesheet">
<style>
  :root {
    --bg: #e9eaec;
    --card: #1a1a1b;
    --card-deep: #111112;
    --cyan: #14a9e1;
    --white: #f4f4f4;
    --grey: #8a8a8a;
  }
  * { box-sizing: border-box; margin: 0; padding: 0; }
  html, body { width: 1200px; height: 913px; overflow: hidden; background: var(--bg); }
  body { position: relative; font-family: "Montserrat", sans-serif; color: var(--white); }

  .card {
    position: absolute;
    width: 720px; height: 412px;
    background: var(--card);
    border-radius: 22px;
    border-bottom: 5px solid var(--cyan);
    border-left: 2px solid var(--cyan);
    box-shadow: 0 10px 26px rgba(0,0,0,.28);
    overflow: hidden;
  }
  .card--back { left: 150px; top: 28px; }
  .card--front { left: 330px; top: 468px; }

  /* back */
  .pattern-field {
    position: absolute; inset: 0;
    background: linear-gradient(115deg, #5a5a5c 0%, #2b2b2d 40%, var(--card-deep) 70%, #1c1c1d 100%);
  }
  .back-brand {
    position: absolute; left: 430px; top: 150px;
    display: flex; align-items: center; gap: 10px;
  }
  .brand-name {
    font-weight: 800; color: var(--cyan); text-transform: uppercase;
    line-height: .92; letter-spacing: .5px;
  }
  .back-brand .brand-name { font-size: 30px; }
  .brand-dot { border: 4px solid var(--grey); border-radius: 50%; flex: none; }
  .back-brand .brand-dot { width: 40px; height: 40px; }

  /* front */
  .front-brand {
    position: absolute; right: 40px; top: 32px;
    display: flex; align-items: center; gap: 16px;
  }
  .front-brand .brand-name { font-size: 50px; text-align: right; }
  .front-brand .brand-dot { width: 72px; height: 72px; border-width: 7px; }

  .services { position: absolute; right: 40px; top: 190px; text-align: right; }
  .services-title { font-weight: 700; color: var(--cyan); font-size: 25px; letter-spacing: .5px; margin-bottom: 6px; }
  .services-list { list-style: none; }
  .services-list li {
    font-size: 17px; font-weight: 500; line-height: 1.45;
    display: flex; justify-content: flex-end; align-items: center; gap: 8px;
  }
  .services-list li::after {
    content: ""; width: 9px; height: 9px; border-radius: 50%;
    border: 2px solid var(--cyan);
  }

  .person { position: absolute; left: 0; top: 160px; }
  .person-bar { position: absolute; left: 0; top: 4px; width: 14px; height: 58px; background: var(--cyan); }
  .person-text { padding-left: 36px; }
  .person-name { font-weight: 800; color: var(--cyan); font-size: 32px; line-height: 1.1; }
  .person-role { font-size: 18px; font-weight: 500; line-height: 1.3; }
  .tagline { font-size: 18px; font-weight: 500; margin-top: 12px; line-height: 1.3; }

  .contacts { list-style: none; margin-top: 12px; }
  .contacts li { display: flex; align-items: center; gap: 10px; font-size: 17px; line-height: 1.45; }
  .contacts svg { width: 15px; height: 15px; flex: none; }
</style>
</head>
<body>

<section class="card card--back" aria-label="Card back">
  <div class="pattern-field" role="img" aria-label="Repeating grid of the brand symbol, embossed, fading from silver to black"></div>
  <div class="back-brand">
    <span class="brand-name">Flood<br>Rescue 360</span>
    <span class="brand-dot"></span>
  </div>
</section>

<section class="card card--front" aria-label="Card front">
  <div class="front-brand">
    <span class="brand-name">Flood<br>Rescue 360</span>
    <span class="brand-dot"></span>
  </div>

  <div class="services">
    <h2 class="services-title">SERVICES</h2>
    <ul class="services-list">
      <li>Water</li>
      <li>Fire</li>
      <li>Mold</li>
      <li>Reconstruction</li>
    </ul>
  </div>

  <div class="person">
    <span class="person-bar"></span>
    <div class="person-text">
      <h1 class="person-name">Marcus Pelley</h1>
      <p class="person-role">General Manager</p>
      <p class="tagline">Urgency for Your Water Emergency!</p>
      <ul class="contacts">
        <li>
          <svg viewBox="0 0 16 16" fill="none" stroke="#f4f4f4" stroke-width="1.6"><rect x="4" y="1" width="8" height="14" rx="1.5"/><line x1="7" y1="12.5" x2="9" y2="12.5"/></svg>
          214-555-0193
        </li>
        <li>
          <svg viewBox="0 0 16 16" fill="#f4f4f4"><path d="M1 6c0-2 3-4 7-4s7 2 7 4l-3 1-1-2H5L4 7zM3 9h10l1 5H2z"/></svg>
          469-555-0148
        </li>
        <li>
          <svg viewBox="0 0 16 16" fill="none" stroke="#f4f4f4" stroke-width="1.6"><rect x="1" y="3" width="14" height="10" rx="1"/><path d="M1 4l7 5 7-5"/></svg>
          Marcus@FloodRescue360.example
        </li>
        <li>
          <svg viewBox="0 0 16 16" fill="none" stroke="#f4f4f4" stroke-width="1.4"><circle cx="8" cy="8" r="6.5"/><ellipse cx="8" cy="8" rx="3" ry="6.5"/><line x1="1.5" y1="8" x2="14.5" y2="8"/></svg>
          FloodRescue360.example
        </li>
      </ul>
    </div>
  </div>
</section>

</body>
</html>
```